BrivoTerna. Lantern of the Steady Harvest. Business card

Professional business card for BrivoTerna (Lantern of the Steady Harvest)
My rationale: Strategy-> Execution-> Results-> Value that lead to the BrivoTerna name: We put the Lantern of the Steady Harvest.
We deliver value to our customers helping them at defining a good strategy (cyan arrow). 90% of well formulated strategies fail due to poor execution so we also consider strategical execution very important (green arrow). Due to the execution we obtain the results (blue arrow). Finally, the results provide feedback to redefine strategy, and the new strategy has to be executed and new results obtained providing new feedback and on and on. It's like a wheel that finally, must create corporate value: value for shareholders, staholders, employees, providers...-

Target Market(s)

CEOs and steering comitees , invewrnent funds

Industry/Entity Type

Business Consultant

Contact Information for Business Card

Teodoro Vinsquel
CEO & Founder
teodoro.vinsquel@brivoterna-example.com
Mobile: +34 655.803.912
www.brivoterna-example.com

Colors

Designer to choose colors to be used in the design.

Requirements
Nice to have
• Nice to hace the words: Strategy, execution, results
• Nice to vave the claim: Lantern of the Steady Harvest
• The three colors should be shown:
• cyan for STRATEGY
• green for EXECUTION
• blue for RESULTS
Should not have
• Complete black background

```html
<!DOCTYPE html>
<html lang="en">
<head>
<meta charset="utf-8">
<title>BrivoTerna – Business Card</title>
<link href="https://fonts.googleapis.com/css2?family=Open+Sans:wght@400;600;700;800&display=swap" rel="stylesheet">
<style>
  :root {
    --stage: #e6e7e9;
    --lime: #9bcb3a;
    --navy: #0f3a9b;
    --royal: #0a3896;
    --cyan: #10aee8;
    --ink: #3c3c3e;
    --text: #2b2b2b;
    --white: #ffffff;
    --rule: #c9ced8;
  }
  * { box-sizing: border-box; margin: 0; padding: 0; }
  html, body {
    width: 1200px; height: 960px; overflow: hidden;
    background: var(--stage);
    font-family: "Open Sans", sans-serif;
  }
  .sheet {
    position: relative; width: 1200px; height: 960px;
    display: flex; flex-direction: column; align-items: center; justify-content: center; gap: 44px;
  }
  .card {
    position: relative; width: 640px; height: 366px; overflow: hidden;
    box-shadow: 0 6px 18px rgba(0,0,0,.18);
  }

  /* Back side */
  .card-back { background: var(--lime); }
  .card-back .brand {
    position: absolute; left: 0; right: 0; top: 128px;
    display: flex; align-items: center; justify-content: center; gap: 14px;
  }
  .card-back .brand-dot { width: 26px; height: 26px; border-radius: 50%; background: var(--ink); }
  .card-back .brand-name { font-size: 54px; font-weight: 800; color: var(--ink); letter-spacing: -1px; }
  .card-back .site {
    position: absolute; left: 0; right: 0; top: 232px; text-align: center;
    font-size: 15px; letter-spacing: 2.5px; color: var(--navy); font-weight: 600;
  }

  /* Front side */
  .card-front { background: var(--white); }
  .bands { position: absolute; left: 0; top: 0; width: 640px; height: 366px; }
  .band-label { font-family: "Open Sans", sans-serif; font-weight: 700; font-size: 17px; }
  .front-brand {
    position: absolute; left: 40px; top: 110px;
    display: flex; align-items: center; gap: 10px;
  }
  .front-brand .brand-dot { width: 20px; height: 20px; border-radius: 50%; background: var(--royal); }
  .front-brand .brand-name { font-size: 38px; font-weight: 800; color: var(--royal); letter-spacing: -1px; }
  .divider { position: absolute; left: 322px; top: 84px; width: 1px; height: 120px; background: var(--rule); }
  .contact { position: absolute; left: 340px; top: 84px; }
  .contact .person { font-size: 21px; font-weight: 700; color: var(--royal); line-height: 1.1; }
  .contact .role { font-size: 13px; color: var(--text); margin-bottom: 10px; }
  .contact ul { list-style: none; }
  .contact li { display: flex; align-items: center; gap: 8px; font-size: 12.5px; color: var(--text); line-height: 21px; }
  .contact svg { width: 13px; height: 13px; flex: none; }
</style>
</head>
<body>
<main class="sheet">

  <section class="card card-back" aria-label="Card back">
    <div class="brand">
      <span class="brand-dot"></span>
      <span class="brand-name">BrivoTerna</span>
    </div>
    <p class="site">www.brivoterna-example.com</p>
  </section>

  <section class="card card-front" aria-label="Card front">
    <svg class="bands" viewBox="0 0 640 366" aria-hidden="true">
      <rect x="0" y="280" width="210" height="86" fill="var(--navy)"/>
      <rect x="214" y="280" width="210" height="86" fill="var(--lime)"/>
      <rect x="428" y="280" width="212" height="86" fill="var(--cyan)"/>
      <path d="M0 0 H640 V300 Q520 292 440 316 Q330 340 214 316 L0 300 Z" fill="var(--white)"/>
      <text class="band-label" x="42" y="336" fill="var(--lime)">Strategy</text>
      <text class="band-label" x="266" y="356" fill="#111">Execution</text>
      <text class="band-label" x="520" y="350" fill="#111">Results</text>
    </svg>

    <div class="front-brand">
      <span class="brand-dot"></span>
      <span class="brand-name">BrivoTerna</span>
    </div>

    <div class="divider"></div>

    <div class="contact">
      <p class="person">Teodoro Vinsquel</p>
      <p class="role">CEO &amp; Founder</p>
      <ul>
        <li>
          <svg viewBox="0 0 14 14"><rect x="3" y="1" width="8" height="12" rx="1.5" fill="none" stroke="var(--cyan)" stroke-width="1.4"/></svg>
          +34 655.803.912
        </li>
        <li>
          <svg viewBox="0 0 14 14"><rect x="1" y="3" width="12" height="8" fill="var(--cyan)"/><path d="M1 3 L7 8 L13 3" fill="none" stroke="#fff" stroke-width="1.2"/></svg>
          teodoro.vinsquel@brivoterna-example.com
        </li>
        <li>
          <svg viewBox="0 0 14 14"><circle cx="7" cy="7" r="5.5" fill="none" stroke="var(--cyan)" stroke-width="1.3"/><ellipse cx="7" cy="7" rx="2.4" ry="5.5" fill="none" stroke="var(--cyan)" stroke-width="1"/><path d="M1.5 7 H12.5" stroke="var(--cyan)" stroke-width="1"/></svg>
          www.brivoterna-example.com
        </li>
      </ul>
    </div>
  </section>

</main>
</body>
</html>
```